Modern design company business card design

We are a design oriented construction firm. The owner is an architect and licensed General Contractor and accomplished furniture designer. We do new home construction and large scale remodeling and office design. We would like a design for our new business cards that is clean and modern, but relatable. We like the bright green color of our logo mixed with different shades of grey. We're also open to reinterpreting the logo.

Target Market(s)

Potential design clients,
Construction clients

Industry/Entity Type

Architecture

Contact Information for Business Card

Tall Maple Design | Build Inc. (optional with logo, Inc. optional)Jeffrey MorganOwner (optional)317.555.0148 cell317.431.8056 officejmorgan@greensquareinc.comwww.greensquareinc.com

Font styles to use
Sans Serif
Other font styles liked:
• Avenir

Requirements
Nice to have
• I like designs that have some continuity between the front and back, i.e. similar layouts or graphic elements that wrap around the card. I tend to prefer horizontal over vertical, but that's not a have to. I also tend to prefer white or recycled paper.

```html
<!DOCTYPE html>
<html lang="en">
<head>
<meta charset="utf-8">
<title>Tall Maple Design | Build — Business Card</title>
<link rel="stylesheet" href="https://fonts.googleapis.com/css2?family=Mulish:ital,wght@0,300;0,400;0,700;0,800;1,400&display=swap">
<style>
  :root {
    --backdrop: #3b3b3b;
    --paper: #ffffff;
    --green-light: #c6dc6a;
    --green-deep: #7cc661;
    --ink: #4f4f4f;
    --ink-soft: #8c8c8c;
    --white: #ffffff;
  }
  * { box-sizing: border-box; margin: 0; padding: 0; }
  html, body {
    width: 1105px; height: 1200px; overflow: hidden;
    background: var(--backdrop);
    font-family: "Mulish", "Avenir", sans-serif;
  }
  .canvas { position: relative; width: 1105px; height: 1200px; }

  .card {
    position: absolute; left: 196px; width: 720px; height: 410px;
    background: var(--paper);
  }
  .card--front { top: 146px; }
  .card--back { top: 603px; }

  /* Front */
  .name-band {
    position: absolute; left: 0; top: 51px; width: 333px; height: 108px;
    background: linear-gradient(to bottom, var(--green-light) 0%, var(--green-light) 55%, var(--green-deep) 100%);
  }
  .accent-square {
    position: absolute; left: 337px; top: 51px; width: 106px; height: 108px;
    background: linear-gradient(to bottom, var(--green-light) 0%, var(--green-light) 55%, var(--green-deep) 100%);
  }
  .holder-name {
    position: absolute; left: 41px; top: 74px;
    font-size: 27px; font-weight: 800; color: var(--white); letter-spacing: -0.2px;
  }
  .holder-title {
    position: absolute; left: 41px; top: 110px;
    font-size: 19px; font-weight: 400; color: var(--white);
  }
  .brand-name {
    position: absolute; right: 44px; top: 126px; text-align: right;
    color: var(--ink-soft); font-weight: 400; line-height: 1;
  }
  .brand-name__main { display: block; font-size: 30px; letter-spacing: 1px; }
  .brand-name__sub { display: block; font-size: 15px; letter-spacing: 1.2px; margin-top: 6px; }

  .contact-list {
    position: absolute; left: 41px; top: 262px; list-style: none;
  }
  .contact-list li {
    display: flex; align-items: center; height: 28px;
    font-size: 20px; color: var(--ink); font-weight: 400;
  }
  .contact-list svg { width: 17px; height: 17px; margin-right: 11px; flex: none; }

  /* Back */
  .back-panel {
    position: absolute; left: 11px; top: 9px; width: 696px; height: 390px;
    background: linear-gradient(to bottom, var(--green-light) 0%, var(--green-light) 58%, var(--green-deep) 100%);
  }
  .back-brand {
    position: absolute; right: 420px; top: 170px; text-align: right;
    color: var(--white); font-weight: 400; line-height: 1;
  }
  .back-brand__line { display: block; font-size: 50px; letter-spacing: 3px; }
  .back-brand__line + .back-brand__line { margin-top: 4px; }
  .back-brand__tag { display: block; font-size: 27px; letter-spacing: 2px; margin-top: 10px; }
  .back-url {
    position: absolute; right: 420px; top: 352px;
    font-size: 17px; font-style: italic; font-weight: 400; color: var(--white);
  }
</style>
</head>
<body>
<main class="canvas">

  <section class="card card--front" aria-label="Business card front">
    <div class="name-band"></div>
    <div class="accent-square"></div>
    <p class="holder-name">Dennis Holloway</p>
    <p class="holder-title">Owner</p>
    <p class="brand-name">
      <span class="brand-name__main">TALL MAPLE</span>
      <span class="brand-name__sub">DESIGN | BUILD</span>
    </p>
    <ul class="contact-list">
      <li>
        <svg viewBox="0 0 16 16" aria-hidden="true"><path fill="#7cc661" d="M3.5 1.5l2.3 0 1.2 3.2-1.6 1.2c.8 1.7 2 2.9 3.7 3.7l1.2-1.6 3.2 1.2v2.3c0 .8-.7 1.5-1.5 1.5C6.5 13 3 9.5 2 4c0-.8.7-2.5 1.5-2.5z"/></svg>
        317.555.0148
      </li>
      <li>
        <svg viewBox="0 0 16 16" aria-hidden="true"><rect x="4" y="1" width="8" height="14" rx="1.5" fill="none" stroke="#7cc661" stroke-width="1.8"/><rect x="7" y="12" width="2" height="1.4" fill="#7cc661"/></svg>
        317.555.0172
      </li>
      <li>
        <svg viewBox="0 0 16 16" aria-hidden="true"><circle cx="8" cy="8" r="7" fill="#7cc661"/><path d="M1.5 8h13M8 1c2.2 2 2.2 12 0 14M8 1c-2.2 2-2.2 12 0 14" stroke="#fff" stroke-width="1" fill="none"/></svg>
        www.tallmapleinc.example
      </li>
      <li>
        <svg viewBox="0 0 16 16" aria-hidden="true"><rect x="1" y="3" width="14" height="10" fill="#7cc661"/><path d="M1.5 3.5L8 9l6.5-5.5" stroke="#fff" stroke-width="1.2" fill="none"/></svg>
        dholloway@tallmapleinc.example
      </li>
    </ul>
  </section>

  <section class="card card--back" aria-label="Business card back">
    <div class="back-panel"></div>
    <p class="back-brand">
      <span class="back-brand__line">TALL</span>
      <span class="back-brand__line">MAPLE</span>
      <span class="back-brand__tag">DESIGN | BUILD</span>
    </p>
    <p class="back-url">www.tallmapleinc.example</p>
  </section>

</main>
</body>
</html>
```